Ashmoor Web Design Project

I need the front page and an internal page designed for this client's website. The logo is attached. Obviously the colors have to go with and/or work with the logo colors. I also attached a very rough brochure layout to help you see the direction we're going in with print materials. The rough site map is also attached. I see a slider on the homepage, the art for which I may come back to you to create. This clinic is in a very high end Dallas neighborhood. The hook is that it's a primary care and urgent facility with convenient hours.

I don't know how much this impacts your design, but this will be a Wordpress site and I'm using a framework called Brovila (brovila.com). If Brovila proves to be inflexible, I'll have to get a template that allows me to execute your design.

This site (http://lanternvaleclinic.com) has the type and quality of content I will eventually have on the Ashmoor site.

I just revised the brief for this project. I added the site map and added details to the overview and the "Must Have" section. Thank you for revisiting the brief. 

Reason: Christmas was a bad time to end it.

Target Market(s)

Women 25-54 with children living at home, income over $150k/year

Industry/Entity Type

Clinic

Requirements
Must have
• Masthead incorporating the logo
Followed by the primary nav
Slider on the home page below that
Dual nav - 1 with the nav in the attached site map
2 secondary nav with areas of healthcare
There will three blocks under the nav
1. It's about time (with a small blurb less than 50 words.
2. It's about choices (with small blurb)
3. It's about you (with small blurb)
Three footer blocks
patient check in link on every page
"No appointment? No problem" icon on every page

```html
<!DOCTYPE html>
<html lang="en">
<head>
<meta charset="utf-8">
<title>Ashmoor Medical</title>
<link href="https://fonts.googleapis.com/css2?family=Lato:wght@400;700&display=swap" rel="stylesheet">
<style>
:root{
  --blue:#1d63ad;
  --blue-dark:#124d8f;
  --blue-head:#1a5b9f;
  --green:#1fa64a;
  --green-text:#18953f;
  --ink:#333;
  --rule:#dcdcdc;
  --panel:#eeeeee;
  --footer:#3a3a3a;
  --link:#1a5fa8;
}
*{box-sizing:border-box;margin:0;padding:0}
html,body{width:946px;height:1200px;overflow:hidden;background:#fff}
body{position:relative;font-family:Arial,Helvetica,sans-serif;color:var(--ink);font-size:8.2px;line-height:12px}
.abs{position:absolute}

/* header */
.masthead{left:0;top:0;width:946px;height:82px;background:#fbfbfb;border-bottom:1px solid var(--rule)}
.brand{left:140px;top:14px;display:flex;align-items:center;gap:6px}
.brand-mark{width:30px;height:30px;border-radius:50%;background:var(--blue)}
.brand-name{font-family:Lato,sans-serif;font-weight:700;font-size:21px;color:var(--blue);line-height:22px}
.brand-tag{left:178px;top:37px;font-size:7px;color:#555;letter-spacing:.2px}
.toplinks{right:140px;top:24px;display:flex;align-items:center;gap:5px;font-size:8px;color:#555}
.toplinks svg{width:13px;height:13px}
.toplinks .sep{color:#999;margin:0 2px}
.social{width:13px;height:13px;border-radius:2px;display:inline-block}

/* hero */
.hero{left:0;top:82px;width:946px;height:296px;background:#fbfaf8;border-bottom:1px solid var(--rule)}
.hero-photo{left:464px;top:126px;width:340px;height:252px;background:radial-gradient(ellipse at 50% 40%,#eae6e2,#d6d4d2 55%,#fbfaf8 80%)}
.hero-title{left:151px;top:164px;font-family:Lato,sans-serif;font-weight:400;font-size:24px;line-height:33px;color:var(--blue-head)}
.hero-title span{color:var(--green)}
.hero-text{left:153px;top:234px;width:310px;font-size:7.6px;line-height:17px}
.dots{left:153px;top:311px;display:flex;gap:1px}
.dots i{width:12px;height:12px;border-radius:3px;background:#999}
.dots i:first-child{background:var(--blue)}

/* nav (above hero) */
.nav{left:140px;top:62px;width:666px;height:43px;background:linear-gradient(#2b78c4,var(--blue-dark));border-radius:4px;display:flex;z-index:5;overflow:hidden}
.nav a{color:#fff;text-decoration:none;font-family:Lato,sans-serif;font-weight:700;font-size:10px;display:flex;align-items:center;justify-content:center;border-right:1px solid rgba(255,255,255,.15);height:100%}
.nav a.active{background:linear-gradient(#2fc35f,var(--green))}
.search{left:664px;top:73px;width:132px;height:22px;background:#fff;border-radius:4px;font-size:7.5px;color:#999;padding:6px 10px;z-index:6}
.search svg{position:absolute;right:10px;top:7px}

/* intro */
h2.sec{font-family:Lato,sans-serif;font-weight:400;font-size:12.5px;color:#333;text-transform:uppercase}
.intro-title{left:140px;top:392px}
.team-photo{left:140px;top:418px;width:152px;height:139px;background:linear-gradient(#e9eef3,#c9d6e3);border:1px solid #ccc}
.intro{left:301px;top:417px;width:290px;font-size:7.6px;line-height:12px;text-align:justify}
.intro p{margin-bottom:12px}
.intro b,.grn{color:var(--green);font-weight:700}
.intro-wide{left:140px;top:567px;width:451px;font-size:7.6px;line-height:12px}
.intro-wide p{margin-bottom:12px}

/* video */
.video{left:606px;top:395px;width:200px;height:124px;background:linear-gradient(#9fb57c,#7c8f63 60%,#5a6b4b)}
.video .bar{position:absolute;left:0;bottom:0;width:100%;height:10px;background:#222}
.video .prog{position:absolute;left:14px;bottom:4px;width:110px;height:2px;background:#d22}
.video .play{position:absolute;left:84px;top:42px;width:32px;height:32px;border:3px solid rgba(255,255,255,.8);border-radius:50%}
.video-text{left:607px;top:526px;width:198px;font-size:7.6px;line-height:13.3px;text-align:justify}

/* appointment tab */
.appt{left:901px;top:431px;width:45px;height:198px;background:var(--green);color:#fff}
.appt span{position:absolute;left:13px;top:156px;transform:rotate(-90deg);transform-origin:left top;font-family:Lato,sans-serif;font-size:11px;white-space:nowrap}
.appt::before{content:"";position:absolute;left:-9px;top:84px;border:9px solid transparent;border-left:0;border-right-color:var(--green)}

/* about blocks */
.block{top:650px;width:142px;height:161px;background:var(--panel)}
.block h3{height:30px;background:var(--blue);color:#fff;font-family:Lato,sans-serif;font-weight:400;font-size:10px;padding:9px 13px}
.block p{padding:9px 12px 0 13px;font-size:7.6px;line-height:12px;text-align:justify;color:#444}
.more{position:absolute;left:13px;bottom:2px;color:var(--link);font-size:7.6px}

/* side boxes */
.sidebox{left:603px;width:203px;border:1px solid #ddd;background:#fff;padding:12px 12px}
.sidebox h3{font-family:Lato,sans-serif;font-weight:400;font-size:12.5px;color:#444;margin-bottom:8px}
.sidebox li{list-style:none;color:var(--green-text);font-size:7.6px;line-height:12px}

/* newsletter */
.news{left:605px;top:895px;width:201px;height:195px;background:linear-gradient(#2d6cb4,#174f94);color:#fff;padding:0 20px}
.news h3{font-family:Lato,sans-serif;font-weight:400;font-size:10.5px;margin:17px 0 0 24px;padding-bottom:7px;border-bottom:1px solid rgba(255,255,255,.25)}
.news svg{position:absolute;left:13px;top:12px}
.news h4{font-size:7.8px;font-weight:400;margin:11px 0 12px}
.news p{font-size:7.6px;line-height:12px;text-align:justify}
.news .email{margin-top:12px;height:20px;background:#fff;border-radius:3px;color:#999;font-size:7.5px;padding:5px 10px}
.news .submit{display:inline-block;margin-top:9px;background:linear-gradient(#2f8be0,#1c6fc2);font-weight:700;font-size:9.5px;padding:6px 10px;border-radius:2px}

/* services */
.svc-title{left:140px;top:822px}
.svc-title span{color:var(--green)}
.svc{width:240px;height:66px}
.svc .pic{position:absolute;left:0;top:0;width:86px;height:65px;border:1px solid #ccc}
.svc h4{position:absolute;left:93px;top:4px;color:var(--green-text);font-size:8px;font-weight:700}
.svc p{position:absolute;left:93px;top:19px;width:110px;font-size:7.6px;line-height:12px;text-align:justify}
.svc p em{font-style:normal;color:var(--link)}

/* footer */
.footer{left:0;top:1167px;width:946px;height:33px;background:var(--footer);color:#aaa;font-size:7.5px}
.footer .links{position:absolute;left:147px;top:11px}
.footer .copy{position:absolute;left:626px;top:11px}
</style>
</head>
<body>

<header class="abs masthead"></header>
<div class="abs brand"><i class="brand-mark"></i><span class="brand-name">Ashmoor Medical</span></div>
<div class="abs brand-tag">— Immediate Family and Personal Care —</div>

<div class="abs toplinks">
  <svg viewBox="0 0 14 14"><path d="M2 12l1-4 7-7 3 3-7 7z" fill="none" stroke="#888" stroke-width="1.2"/></svg>
  <span>Register</span><span class="sep">|</span>
  <svg viewBox="0 0 14 14"><circle cx="7" cy="4.5" r="3" fill="#999"/><path d="M1 14c0-4 3-6 6-6s6 2 6 6z" fill="#999"/></svg>
  <span>Login</span><span class="sep">|</span>
  <svg viewBox="0 0 14 14"><rect x="1" y="2" width="12" height="8" rx="1" fill="none" stroke="#888"/><path d="M4 10l0 3 3-3" fill="none" stroke="#888"/></svg>
  <span>Blog</span><span class="sep">|</span>
  <span class="social" style="background:#3b5a98"></span>
  <span class="social" style="background:#2fa9e0"></span>
  <span class="social" style="background:#d03a2a"></span>
</div>

<section class="abs hero"></section>
<div class="abs hero-photo" role="img" aria-label="Smiling doctor in a white coat with a family standing behind him"></div>
<h1 class="abs hero-title">Concierge - Quality healthcare...<br><span>... for your whole family</span></h1>
<p class="abs hero-text">Aenean feugiat, risus vitae accumsan egestas, mi massa ullamcorper lectus, faucibus sollicitudin enim lacus at urna. Nunc nec aliquam mauris. Donec non neque at massa euismod lacinia. Morbi pharetra enim nec justo tincidunt bibendum.</p>
<div class="abs dots"><i></i><i></i><i></i><i></i></div>

<nav class="abs nav">
  <a style="width:66px">HOME</a>
  <a style="width:64px">ABOUT</a>
  <a class="active" style="width:72px">SERVICES</a>
  <a style="width:62px">STAFF</a>
  <a style="width:84px">INSURANCE</a>
  <a style="width:67px">VIDEOS</a>
  <a style="width:90px;border-right:0">CONTACT US</a>
</nav>
<div class="abs search">Search
  <svg width="8" height="8" viewBox="0 0 8 8"><circle cx="3.2" cy="3.2" r="2.4" fill="none" stroke="#999"/><path d="M5 5l2.5 2.5" stroke="#999"/></svg>
</div>

<h2 class="abs sec intro-title">We care about the health of you and your family</h2>
<div class="abs team-photo" role="img" aria-label="Group of smiling doctors and nurses"></div>
<div class="abs intro">
  <p><b>Ashmoor family medical</b> is a full service medical facility with in-house lab and X-ray. We are here to take care of your medical needs whether they be family practice, urgent care or occupational in nature. Our providers and staff are eager to assist patients in a friendly efficient manner.</p>
  <p>Ashmoor family medical director is also the chief clinician and owner. <b>Dr. Elias Varnholt,</b> position as a clinician and director allows him to manage patients and be involved in the day to day operation of his practice. This means there is a continual staff emphasis on excellent patient care.</p>
  <p>Our facility is conveniently located in the north Dallas area, just drive right up to the front door. By choosing us, you become an important part of our health care team.</p>
</div>
<div class="abs intro-wide">
  <p>We encourage you to ask questions and take an interest in getting well and staying well.</p>
  <p>Please browse the website for more details about our services. Your health and well being is our number one priority. We would appreciate the opportunity to answer any questions you might have, <span class="grn">please call at (555) 014 2290</span> to schedule a consultation today, or just come by, no appointment is required.</p>
</div>

<div class="abs video" role="img" aria-label="Video still of a happy family">
  <span class="play"></span><span class="bar"></span><span class="prog"></span>
</div>
<p class="abs video-text">Cras dictum metus quis tortor sollicitudin sagittis. Nulla nec massa et enim tincidunt ornare pharetra imperdiet massa. Suspendisse potenti. In hac habitasse platea dictumst. Nullam et enim purus, a cursus nibh. Ut consectetur, tortor consequat dignissim scelerisque, magna eros ullamcorper sem, vitae pretium purus lacus eu massa.</p>

<div class="abs appt"><span>APPOINTMENT REQUEST</span>
  <svg style="position:absolute;left:14px;top:173px" width="20" height="20" viewBox="0 0 20 20"><circle cx="10" cy="10" r="9" fill="#fff"/><circle cx="10" cy="10" r="7" fill="none" stroke="#aaa"/><path d="M10 5v5l3 2" stroke="#666" fill="none"/></svg>
</div>

<div class="abs block" style="left:140px"><h3>IT'S ABOUT TIME</h3><p>Pellentesque tincidunt est vitae mauris adipiscing sagittis. In hac habitasse platea dictumst. Vestibulum vitae arcu eget nulla venenatis fringilla a in neque. Sed ut lorem ipsum, quis consequat magna. Fusce lacinia orci quis risus tincidunt.</p><span class="more">more....</span></div>
<div class="abs block" style="left:295px"><h3>IT'S ABOUT CHOICES</h3><p>In hac habitasse platea dictumst. Vestibulum vitae arcu eget nulla venenatis fringilla a in neque. Sed ut lorem ipsum, quis consequat magna. Fusce lacinia orci quis risus tincidunt. Pellentesque tincidunt est vitae mauris adipiscing sagittis.</p><span class="more">more....</span></div>
<div class="abs block" style="left:449px"><h3>IT'S ABOUT YOU</h3><p>Arcu eget nulla venenatis fringilla a in neque. Sed ut lorem ipsum, quis consequat magna. Fusce lacinia orci quis risus tincidunt. Pellentesque tincidunt est vitae mauris adipiscing sagittis. In hac habitasse platea dictumst. Vestibulum vitae .</p><span class="more">more....</span></div>

<div class="abs sidebox" style="top:636px;height:122px"><h3>CONCIERGE CONVENIENCE</h3><ul>
<li>Walk-ins welcome</li><li>Major credit cards accepted</li><li>Evening and weekend hours</li><li>Most Insurance accepted and filled for you</li><li>Cosmetic procedures performed by the doctor</li><li>In-house digital imaging and complete lab</li></ul></div>
<div class="abs sidebox" style="top:766px;height:121px"><h3>EXPERT MEDICAL CARE</h3><ul>
<li>Advanced Adult &amp; Pediatric Family Care</li><li>Immediate Care for Minor Emergencies</li><li>Womens Health &amp; Beauty</li><li>Medical Spa Treatements (Lumera®,Dermaven®)</li><li>Men's Health (Low-T, Executive Physicals)</li><li>Medically Supervised Weight Loss and Much More</li></ul></div>

<div class="abs news">
  <svg width="26" height="24" viewBox="0 0 26 24"><rect x="1" y="8" width="24" height="15" fill="#e8eef5"/><path d="M1 8l12 8 12-8" fill="none" stroke="#aab"/><rect x="6" y="2" width="14" height="10" fill="#fff"/></svg>
  <h3>NEWSLETTER</h3>
  <h4>FREE ON-LINE CONSULTATION</h4>
  <p>Nalesuada odiorbi nuravida acursus neuc aloreasma. Maecenas tristique orci ac sem. Duis ultriciearet radertas magna.</p>
  <div class="email">Email Address</div>
  <span class="submit">SUBMIT</span>
</div>

<h2 class="abs sec svc-title">Our <span>Services</span></h2>
<div class="abs svc" style="left:140px;top:850px"><div class="pic" role="img" aria-label="Surgeons in an operating room" style="background:linear-gradient(#4aa0a8,#1f5c68)"></div><h4>IMMEDIATE CARE</h4><p>Sed dictum ultricies odio, sit amet commodo lacus tempus vitae. Fusce lacinia eros nec velit blandit . <em>more....</em></p></div>
<div class="abs svc" style="left:377px;top:850px"><div class="pic" role="img" aria-label="Close-up of irritated eyes" style="background:linear-gradient(#d9b8a4,#9c7662)"></div><h4>ALLERGIES</h4><p>Sed dictum ultricies odio, sit amet commodo lacus tempus vitae. Fusce lacinia eros nec velit blandit . <em>more....</em></p></div>
<div class="abs svc" style="left:140px;top:936px"><div class="pic" role="img" aria-label="Doctor examining a child" style="background:linear-gradient(#e9d8c8,#b88c6e)"></div><h4>PRIMARY CARE</h4><p>Sed dictum ultricies odio, sit amet commodo lacus tempus vitae. Fusce lacinia eros nec velit blandit . <em>more....</em></p></div>
<div class="abs svc" style="left:377px;top:936px"><div class="pic" role="img" aria-label="Medical staff attending a patient" style="background:linear-gradient(#cfd6dc,#8a98a6)"></div><h4>WOMEN'S HEALTH</h4><p>Sed dictum ultricies odio, sit amet commodo lacus tempus vitae. Fusce lacinia eros nec velit blandit . <em>more....</em></p></div>
<div class="abs svc" style="left:140px;top:1026px"><div class="pic" role="img" aria-label="Patient entering a scanner" style="background:linear-gradient(#d8d4d8,#8e8a96)"></div><h4>MEN'S HEALTH</h4><p>Sed dictum ultricies odio, sit amet commodo lacus tempus vitae. Fusce lacinia eros nec velit blandit . <em>more....</em></p></div>
<div class="abs svc" style="left:377px;top:1026px"><div class="pic" role="img" aria-label="Measuring tape around a waist" style="background:linear-gradient(#e8d2c6,#8fb3d6)"></div><h4>WEIGHT LOSS</h4><p>Sed dictum ultricies odio, sit amet commodo lacus tempus vitae. Fusce lacinia eros nec velit blandit . <em>more....</em></p></div>

<footer class="abs footer">
  <span class="links">Home | About | Services | Staff | Insurance | Videos | Contact us</span>
  <span class="copy">© 2012 | Ashmoor Medical | All Rights Reserved</span>
</footer>

</body>
</html>
```